Wrenfield Pharmacy opening

We want to have a double sided 5.5"x8.5" flyer for a new Pharmacy opening in a well known strip mall in the neighborhood and we are planning to mail it to neighbors homes.

Want to put the outside pharmacy picture on the main side of the flyer and a coupon with 25% off towards an OTC product on the back in addition to the info below (preferably in a sort of bulletin points not a list (something like the 2 examples attached).

Colors to be red like the exterior sign and blue like the interior wall paint:

Front side should have:
Wrenfield pharmacy
Your locally owned and operated pharmacy around the corner.
317-4821 Ostrander rd.
Pike hollow plaza
T. 555 206 3379 (call or text)
F. 555-206-3381

Free prescription delivery
Text us for refills
Specialized compounding
Customized compression stockings

The back side should have:

Do you forget taking your medications! We offer multiple compliance packaging options at no additional cost.
Had shingles before or worried to have it? travelling soon? check our vaccinations options!
Suffering side effects? We are experienced to check your medications interactions & different coverage options.
Hard time monitoring your blood pressure? Trying to stop smoking? we can always help.

FEELING BETTER STARTS HERE

```html
<!DOCTYPE html>
<html lang="en">
<head>
<meta charset="utf-8">
<title>Wrenfield Pharmacy Flyer</title>
<link href="https://fonts.googleapis.com/css2?family=Montserrat:wght@400;500;600;700;800&family=Signika:wght@400;500;600&display=swap" rel="stylesheet">
<style>
:root{
  --red:#b5242c;
  --red-deep:#9e1d25;
  --blue:#50689a;
  --ink:#3d3d3d;
  --board:#cfcfd1;
  --paper:#f1f1f2;
  --white:#ffffff;
}
*{margin:0;padding:0;box-sizing:border-box}
html,body{width:1200px;height:985px;overflow:hidden;background:var(--board)}
body{position:relative;font-family:"Montserrat",sans-serif;color:var(--ink)}
.sheet{position:absolute;top:72px;width:517px;height:798px;overflow:hidden;box-shadow:4px 6px 14px rgba(0,0,0,.28)}
.sheet--front{left:74px;background:var(--red)}
.sheet--back{left:609px;background:var(--paper)}
.side-label{position:absolute;font-size:14px;letter-spacing:1px;color:#333;transform:rotate(-90deg);transform-origin:left top}
.side-label--front{left:49px;top:870px}
.side-label--back{left:1141px;top:870px}
.caption{position:absolute;top:913px;width:1200px;text-align:center;font-size:14px;color:#222}

/* front */
.storefront{position:absolute;left:0;top:0;width:517px;height:460px;background:linear-gradient(180deg,#1c1c1c 0%,#3a3838 18%,#8c8780 40%,#5d6068 62%,#3c3f44 80%,#6b6a68 100%)}
.red-field{position:absolute;left:0;top:0}
.brand{position:absolute;left:114px;top:34px;display:flex;align-items:center;gap:14px}
.brand-dot{width:74px;height:74px;border-radius:50%;background:var(--white);border:5px solid var(--red)}
.brand-name{font-weight:700;font-size:27px;line-height:29px;color:var(--white);letter-spacing:1px}
.service{position:absolute;top:385px;width:120px;text-align:center}
.service-icon{display:block;margin:0 auto}
.service-label{margin-top:9px;font-family:"Signika",sans-serif;font-weight:500;font-size:14px;line-height:16px;color:var(--white)}
.offer{position:absolute;left:33px;top:534px;font-weight:800;font-size:58px;line-height:62px;color:var(--white);letter-spacing:-1px}
.offer-tag{position:absolute;left:33px;top:598px;width:213px;height:24px;background:var(--blue);color:var(--white);font-weight:500;font-size:15px;line-height:24px;text-align:center}
.tagline{position:absolute;left:35px;top:637px;font-size:19.5px;line-height:22px;color:var(--white)}
.tagline b{font-weight:700}
.pharmacist{position:absolute;left:312px;top:527px;width:205px;height:271px;background:radial-gradient(ellipse at 55% 30%,#d9b39a 0%,#c7a08a 22%,#f3f3f3 48%,#e6e6e6 100%)}
.contact-band{position:absolute;left:0;top:725px;width:517px;height:73px;background:var(--paper)}
.contact-line{position:absolute;left:32px;display:flex;align-items:center;gap:6px}
.contact-line--phone{top:740px;font-size:15px;font-weight:500;color:#333}
.contact-line--phone strong{font-size:21px;font-weight:700;color:var(--blue);margin-left:4px}
.contact-line--address{top:770px;font-size:12px;color:#333}

/* back */
.back-art{position:absolute;left:0;top:0}
.headline{position:absolute;top:40px;width:517px;text-align:center;font-weight:500;font-size:25px;line-height:29px;color:var(--white)}
.bubble{position:absolute;width:96px;height:96px;margin:-48px 0 0 -48px;border-radius:50%;background:var(--white);border:2px solid var(--red);display:flex;align-items:center;justify-content:center;text-align:center;font-family:"Signika",sans-serif;font-weight:500;font-size:12.5px;line-height:14px;color:var(--red);padding:0 8px}
.center-mark{position:absolute;left:211px;top:305px;width:108px;height:108px;border-radius:50%;background:var(--white);border:3px solid var(--red);display:flex;align-items:center;justify-content:center;text-align:center;font-weight:700;font-size:11px;line-height:13px;color:var(--red)}
.help{position:absolute;top:581px;width:517px;text-align:center;font-weight:600;font-size:25px;color:var(--red)}
.packaging{position:absolute;top:615px;width:517px;text-align:center;font-weight:500;font-size:16.5px;line-height:20px;color:var(--blue)}
.interactions{position:absolute;top:672px;width:517px;text-align:center;font-size:12.5px;line-height:16px;color:#333}
.slogan{position:absolute;left:66px;top:724px;width:384px;height:35px;background:var(--blue);color:var(--white);font-weight:700;font-size:19px;line-height:35px;text-align:center;letter-spacing:.5px}
</style>
</head>
<body>

<section class="sheet sheet--front">
  <div class="storefront" role="img" aria-label="Photo of the pharmacy storefront in the strip mall with its red exterior sign"></div>
  <svg class="red-field" width="517" height="798" viewBox="0 0 517 798" aria-hidden="true">
    <path d="M0 399 Q258 470 517 399 L517 798 L0 798Z" fill="var(--red)"/>
  </svg>

  <div class="brand">
    <span class="brand-dot"></span>
    <div class="brand-name">WRENFIELD<br>PHARMACY</div>
  </div>

  <div class="service" style="left:40px">
    <svg class="service-icon" width="70" height="70" viewBox="0 0 70 70" aria-hidden="true">
      <circle cx="35" cy="35" r="34" fill="#fff"/><circle cx="35" cy="35" r="30" fill="none" stroke="var(--red)" stroke-width="1.5"/>
      <g fill="none" stroke="var(--red)" stroke-width="2" stroke-linejoin="round">
        <path d="M24 26h22v17H24zM46 31h7l5 6v6H46z"/><circle cx="30" cy="45" r="3"/><circle cx="51" cy="45" r="3"/>
        <path d="M12 30h9M14 35h7M16 40h5"/>
      </g>
    </svg>
    <div class="service-label">Free prescription delivery</div>
  </div>

  <div class="service" style="left:148px">
    <svg class="service-icon" width="70" height="70" viewBox="0 0 70 70" aria-hidden="true">
      <circle cx="35" cy="35" r="34" fill="#fff"/><circle cx="35" cy="35" r="30" fill="none" stroke="var(--red)" stroke-width="1.5"/>
      <g fill="none" stroke="var(--red)" stroke-width="2" stroke-linejoin="round">
        <rect x="22" y="16" width="20" height="36" rx="3"/><path d="M30 47h4"/>
        <path d="M34 25h16v11h-9l-4 4v-4h-3z"/><path d="M38 29h8M38 32h6"/>
      </g>
    </svg>
    <div class="service-label">Text us<br>for refills</div>
  </div>

  <div class="service" style="left:256px">
    <svg class="service-icon" width="70" height="70" viewBox="0 0 70 70" aria-hidden="true">
      <circle cx="35" cy="35" r="34" fill="#fff"/><circle cx="35" cy="35" r="30" fill="none" stroke="var(--red)" stroke-width="1.5"/>
      <g fill="none" stroke="var(--red)" stroke-width="2" stroke-linejoin="round">
        <path d="M16 33h38c0 10-8 17-19 17S16 43 16 33z"/><path d="M26 50l-2 4h22l-2-4"/>
        <path d="M40 30l10-12 3 2-9 12"/><path d="M24 31c0-5 3-8 7-8M30 31c1-4 4-6 8-5"/>
      </g>
    </svg>
    <div class="service-label">Specialized<br>compounding</div>
  </div>

  <div class="service" style="left:366px">
    <svg class="service-icon" width="70" height="70" viewBox="0 0 70 70" aria-hidden="true">
      <circle cx="35" cy="35" r="34" fill="#fff"/><circle cx="35" cy="35" r="30" fill="none" stroke="var(--red)" stroke-width="1.5"/>
      <g fill="none" stroke="var(--red)" stroke-width="2" stroke-linejoin="round">
        <path d="M28 14h12v22l10 8c2 2 1 6-2 6H34c-4 0-6-3-6-6z"/><path d="M28 22h12M28 29h12"/>
      </g>
    </svg>
    <div class="service-label">Customized compression stockings</div>
  </div>

  <div class="offer">25%off</div>
  <div class="offer-tag">Towards an OTC product</div>
  <p class="tagline">Your <b>locally owned</b> &amp;<br><b>operated pharmacy</b><br>around the corner.</p>

  <div class="contact-band"></div>
  <div class="pharmacist" role="img" aria-label="Photo of a smiling pharmacist in a white coat pointing toward the offer"></div>
  <div class="contact-line contact-line--phone">
    <svg width="13" height="13" viewBox="0 0 24 24" aria-hidden="true"><path d="M6.6 10.8a15 15 0 006.6 6.6l2.2-2.2c.3-.3.7-.4 1-.2 1.1.4 2.3.6 3.6.6.6 0 1 .4 1 1V20c0 .6-.4 1-1 1A17 17 0 013 4c0-.6.4-1 1-1h3.5c.6 0 1 .4 1 1 0 1.3.2 2.5.6 3.6.1.3 0 .7-.2 1z" fill="var(--blue)"/></svg>
    Call us or Text <strong>555 206 3379</strong>
  </div>
  <div class="contact-line contact-line--address">
    <svg width="11" height="13" viewBox="0 0 20 24" aria-hidden="true"><path d="M10 0a8 8 0 00-8 8c0 6 8 16 8 16s8-10 8-16a8 8 0 00-8-8zm0 11a3 3 0 110-6 3 3 0 010 6z" fill="var(--blue)"/></svg>
    317-4821 Ostrander rd. Pike hollow plaza
  </div>
</section>

<section class="sheet sheet--back">
  <svg class="back-art" width="517" height="798" viewBox="0 0 517 798">
    <path d="M0 0H517V336 Q470 330 440 320 L80 320 Q40 330 0 336Z" fill="var(--red)"/>
    <circle cx="259" cy="356" r="197" fill="none" stroke="#ffffff" stroke-width="2" opacity=".9"/>
    <circle cx="259" cy="356" r="181" fill="url(#shelves)" stroke="#ffffff" stroke-width="3" role="img" aria-label="Photo of the pharmacy interior with blue wall and stocked shelves"/>
    <defs>
      <linearGradient id="shelves" x1="0" y1="0" x2="0" y2="1">
        <stop offset="0" stop-color="#d9d6cf"/>
        <stop offset=".3" stop-color="#3f5a96"/>
        <stop offset=".55" stop-color="#e6ddcc"/>
        <stop offset="1" stop-color="#d8cbb4"/>
      </linearGradient>
    </defs>
  </svg>

  <h2 class="headline">Do you forget<br>taking your medications?</h2>

  <div class="bubble" style="left:204px;top:183px">Hard time monitoring your blood pressure?</div>
  <div class="bubble" style="left:322px;top:183px">Trying<br>to stop<br>smoking?</div>
  <div class="bubble" style="left:108px;top:241px">Suffering side effects?</div>
  <div class="bubble" style="left:413px;top:241px">Travelling soon?</div>
  <div class="bubble" style="left:78px;top:348px">Had shingles before or worried to have it?</div>
  <div class="bubble" style="left:448px;top:348px">check our vaccinations options!</div>

  <div class="center-mark">WRENFIELD<br>PHARMACY</div>

  <p class="help">We can always help.</p>
  <p class="packaging">We offer multiple compliance packaging<br>options at no additional cost.</p>
  <p class="interactions">We are experienced to check your medications<br>interactions &amp; different coverage options.</p>
  <div class="slogan">FEELING BETTER STARTS HERE</div>
</section>

<span class="side-label side-label--front">FRONT</span>
<span class="side-label side-label--back">BACK</span>
<p class="caption">Design Concept Wrenfield Pharmacy Flyer 01</p>

</body>
</html>
```